Marlow Estate Fixers (Handyman / Home Improvement Company)

Looking for a double sided professional looking business card with Logo attached to be highlighted on one side and throwing in an image of a handyman as an option would be nice to see as well. We are a company focused on providing quality Handyman and Home improvement services in a timely manner that is done right the first time with integrity

Industry/Entity Type

Handyman / Home Improvement

Contact Information for Business Card

(LOGO, Name, Mobile and office phone numbers, email) on front side of card, (the words "The SOLUTION to all of your Handyman and Home Improvement needs" followed by "Family Owned and Operated" at the very bottom) on the back.

Colors
EB3D1F
EC4F4E
F09395
F8D3D4
FCEDEE

Requirements
Must have
• Red, Gray, Black Color scheme
Should not have
• No Yellow or Blue colors

```html
<!DOCTYPE html>
<html lang="en">
<head>
<meta charset="UTF-8">
<title>Marlow Estate Fixers – Business Card</title>
<link rel="stylesheet" href="https://fonts.googleapis.com/css2?family=Poppins:wght@300;400;500;600;700&display=swap">
<style>
  :root {
    --stage: #232323;
    --card: #1f1f22;
    --card-deep: #161618;
    --pattern-light: #2c2c30;
    --pattern-dark: #19191b;
    --emboss: #2a2a2d;
    --red: #eb3d1f;
    --red-soft: #ec4f4e;
    --white: #ffffff;
    --grey: #d8d8da;
  }
  * { margin: 0; padding: 0; box-sizing: border-box; }
  html, body {
    width: 1200px; height: 800px; overflow: hidden;
    background: var(--stage);
    font-family: "Poppins", sans-serif;
  }
  .canvas {
    position: relative; width: 1200px; height: 800px;
    display: flex; align-items: center; justify-content: center; gap: 40px;
  }
  .card {
    position: relative; width: 540px; height: 309px;
    border-radius: 22px; overflow: hidden;
    background: var(--card);
    border: 3px solid var(--red);
    box-shadow: 0 14px 30px rgba(0,0,0,.45);
  }

  /* Brand side */
  .card--brand .pattern {
    position: absolute; inset: 0;
    background:
      radial-gradient(circle at 50% 45%, var(--pattern-light) 0%, var(--pattern-dark) 75%);
  }
  .brand-mark {
    position: absolute; left: 0; right: 0; top: 92px;
    display: flex; align-items: center; justify-content: center; gap: 12px;
  }
  .brand-mark__dot {
    width: 22px; height: 22px; border-radius: 50%; background: var(--red);
  }
  .brand-mark__name {
    font-weight: 700; font-size: 34px; color: var(--white); letter-spacing: .5px;
  }
  .brand-motto {
    position: absolute; left: 0; right: 0; top: 178px;
    text-align: center; font-size: 15px; font-weight: 400; color: var(--red-soft);
  }
  .brand-tagline {
    position: absolute; left: 0; right: 0; top: 212px;
    text-align: center; font-size: 14px; font-weight: 400; color: var(--white);
  }

  /* Contact side */
  .card--contact .emboss-name {
    position: absolute; left: 26px; top: 40px; width: 250px;
    font-weight: 700; font-size: 48px; line-height: 1.05;
    color: var(--emboss);
  }
  .accent-bar {
    position: absolute; right: 0; top: 36px; width: 18px; height: 48px;
    background: var(--red);
  }
  .person {
    position: absolute; right: 34px; top: 34px; text-align: right;
  }
  .person__name { font-size: 32px; line-height: 1.1; color: var(--red); }
  .person__first { font-weight: 700; }
  .person__last { font-weight: 300; }
  .person__role { font-size: 15px; font-weight: 600; color: var(--white); }

  .address {
    position: absolute; right: 34px; top: 126px; text-align: right;
    font-size: 14px; line-height: 1.4; color: var(--white); font-style: normal;
  }
  .contact-list {
    position: absolute; right: 22px; top: 184px; list-style: none;
  }
  .contact-list li {
    display: flex; align-items: center; justify-content: flex-end; gap: 8px;
    font-size: 14px; line-height: 1.45; color: var(--white);
  }
  .contact-list .hl { color: var(--red); }
  .contact-list svg { width: 14px; height: 14px; flex: none; }
</style>
</head>
<body>
<main class="canvas">

  <section class="card card--brand" aria-label="Business card, brand side">
    <div class="pattern" role="img" aria-label="Repeating embossed brand pattern across the card"></div>
    <div class="brand-mark">
      <span class="brand-mark__dot"></span>
      <span class="brand-mark__name">Marlow Estate Fixers</span>
    </div>
    <p class="brand-motto">Family Owned and Operated</p>
    <p class="brand-tagline">Your SOLUTION to all of your Handyman and Home Improvement needs</p>
  </section>

  <section class="card card--contact" aria-label="Business card, contact side">
    <p class="emboss-name">Marlow Estate Fixers</p>
    <span class="accent-bar"></span>

    <div class="person">
      <p class="person__name"><span class="person__first">Dana</span> <span class="person__last">Rourke</span></p>
      <p class="person__role">Founder &amp; CEO</p>
    </div>

    <address class="address">
      418 Elmstead Ave. Suite 120<br>
      Harlow Springs, TX 75990
    </address>

    <ul class="contact-list">
      <li>(555) 214-3086
        <svg viewBox="0 0 14 14" aria-hidden="true"><rect x="3.5" y="1" width="7" height="12" rx="1.5" fill="none" stroke="var(--red)" stroke-width="1.3"/></svg>
      </li>
      <li>(555) 214-7700
        <svg viewBox="0 0 14 14" aria-hidden="true"><path d="M3 1.5l2.2 2.6-1.2 1.5c.8 1.7 2 2.9 3.6 3.7l1.5-1.2 2.6 2.2-1.3 2C6 11.8 2.2 8 1 3.1z" fill="var(--red)"/></svg>
      </li>
      <li><span>www.<span class="hl">marlowfixers</span>.com</span>
        <svg viewBox="0 0 14 14" aria-hidden="true"><circle cx="7" cy="7" r="5.6" fill="none" stroke="var(--red)" stroke-width="1.3"/><path d="M1.4 7h11.2M7 1.4c-2.4 3-2.4 8.2 0 11.2M7 1.4c2.4 3 2.4 8.2 0 11.2" fill="none" stroke="var(--red)" stroke-width="1"/></svg>
      </li>
      <li><span>info@<span class="hl">marlowfixers</span>.com</span>
        <svg viewBox="0 0 14 14" aria-hidden="true"><rect x="1" y="3" width="12" height="8.5" rx="1" fill="none" stroke="var(--red)" stroke-width="1.3"/><path d="M1.5 3.5L7 8l5.5-4.5" fill="none" stroke="var(--red)" stroke-width="1.3"/></svg>
      </li>
    </ul>
  </section>

</main>
</body>
</html>
```